Flyer Design for Private Car Service

Flyer should cater to Business Travelers and Executives who travel Business Class or First Class.
Flyer should include images attached.
Flyer should include the below text
Dallas to Austin
Quorvan Ride
• Travel Dallas to Austin in a new 2025 Norvak Tressel for $499 one-way
• Trip includes a Uniformed Chauffeur who has a Commercial Drivers License (CDL)
• You can Schedule Chauffeur Pickup at Your Home in Dallas
• Our Chauffeur will Drop You Off at Your Final Destination in Austin
• You can Schedule Chauffeur Return Pickup in Austin and Return Back to Dallas.
• We offer Faster Times on Door-to-Door Travel than Bluequill Airways
• We offer Comparable Prices on Door-to-Door Travel Times than Bluequill Airways
• All of our trips are insured with $500k of commercial auto insurance
• Our Passengers can Talk on Cell Phone & Conduct Kavlo calls Throughout Travel
• Our Passengers have Maximum Privacy, Comfort and First-Class Amenities.
• Our Passengers Avoid Marrow Pike Airfield and QHN Airport hassles & delays
• Member Tellbrook Chamber of Commerce, Pindle Chamber of Commerce.
• Book your trip today at www.quorvanride.example
Target Market(s)
Business Travelers
Look and feel

```html
<!DOCTYPE html>
<html lang="en">
<head>
<meta charset="utf-8">
<title>Quorvan Ride – Dallas to Austin</title>
<link href="https://fonts.googleapis.com/css2?family=Open+Sans:wght@400;600;800&display=swap" rel="stylesheet">
<style>
  :root {
    --red: #e8283a;
    --ink: #111111;
    --text-grey: #4f4f4f;
    --paper: #fbfbfb;
    --photo-light: #cfcac8;
    --photo-mid: #8f8a89;
    --photo-dark: #4a4646;
    --white: #ffffff;
  }
  * { margin: 0; padding: 0; box-sizing: border-box; }
  html, body { width: 927px; height: 1200px; overflow: hidden; background: var(--white); }
  .flyer {
    position: relative;
    width: 927px;
    height: 1200px;
    overflow: hidden;
    font-family: "Open Sans", sans-serif;
    background: linear-gradient(180deg, #f6f6f6 0%, #eeeeee 55%, #f2f2f2 100%);
  }
  .hero-photo {
    position: absolute;
    left: 0; top: 0;
    width: 927px; height: 530px;
    background:
      linear-gradient(180deg, var(--photo-light) 0%, #bdb8b6 22%, var(--photo-dark) 30%, #5a5555 40%, var(--photo-mid) 55%, #a19d9c 75%, #b4b0ae 100%);
  }
  .body-fade {
    position: absolute;
    left: 0; top: 500px;
    width: 927px; height: 600px;
    background: linear-gradient(180deg, rgba(255,255,255,0.95), rgba(236,236,236,0.9) 50%, rgba(245,245,245,0.95));
  }
  .brand {
    position: absolute;
    left: 48px; top: 58px;
    width: 200px;
    text-align: center;
    color: var(--ink);
  }
  .brand-name {
    display: block;
    font-weight: 600;
    font-size: 26px;
    letter-spacing: 1px;
    line-height: 32px;
  }
  .route-title {
    display: block;
    font-weight: 600;
    font-size: 13px;
    letter-spacing: 2px;
    text-transform: uppercase;
    line-height: 20px;
  }
  .curve-divider { position: absolute; left: 0; top: 470px; }
  .center-mark {
    position: absolute;
    left: 0; top: 420px;
    width: 927px;
    display: flex; justify-content: center; align-items: center; gap: 12px;
  }
  .center-mark .dot { width: 22px; height: 22px; border-radius: 50%; background: var(--red); }
  .center-mark .name { font-weight: 600; font-size: 30px; color: var(--ink); letter-spacing: 1px; }
  .features {
    position: absolute;
    left: 0; top: 572px;
    width: 927px;
    list-style: none;
    text-align: center;
    color: var(--text-grey);
    font-size: 17.5px;
    line-height: 44px;
    z-index: 2;
  }
  .features li::before { content: "• "; }
  .footer-band { position: absolute; left: 0; top: 1040px; z-index: 1; }
  .cta {
    position: absolute;
    left: 0; top: 1160px;
    width: 927px;
    text-align: center;
    color: var(--white);
    font-weight: 800;
    font-size: 22px;
    z-index: 2;
  }
  .cta .url { text-decoration: underline; text-underline-offset: 3px; }
  .ref-code {
    position: absolute;
    right: 17px; top: 1168px;
    color: var(--white);
    font-size: 11px;
    z-index: 2;
  }
</style>
</head>
<body>
<div class="flyer">
  <div class="hero-photo" role="img" aria-label="Four uniformed chauffeurs standing beside black, white and red SUVs in front of a modern building"></div>
  <div class="body-fade" role="img" aria-label="Faded background of a chauffeur opening an SUV door"></div>

  <div class="brand">
    <span class="brand-name">Quorvan Ride</span>
    <span class="route-title">Dallas to Austin</span>
  </div>

  <svg class="curve-divider" width="927" height="80" viewBox="0 0 927 80" aria-hidden="true">
    <path d="M0 50 Q463 -10 927 50 L927 80 L0 80 Z" fill="#fbfbfb" opacity="0.96"/>
    <path d="M0 50 Q463 -10 927 50" fill="none" stroke="var(--red)" stroke-width="2"/>
  </svg>

  <div class="center-mark">
    <span class="dot"></span>
    <span class="name">Quorvan Ride</span>
  </div>

  <ul class="features">
    <li>Travel Dallas to Austin in a new 2025 Norvak Tressel for $499 one-way</li>
    <li>Trip includes a Uniformed Chauffeur who has a Commercial Drivers License (CDL)</li>
    <li>You can Schedule Chauffeur Pickup at Your Home in Dallas</li>
    <li>Our Chauffeur will Drop You Off at Your Final Destination in Austin</li>
    <li>You can Schedule Chauffeur Return Pickup in Austin and Return Back to Dallas.</li>
    <li>We offer Faster Times on Door-to-Door Travel than Bluequill Airways</li>
    <li>We offer Comparable Prices on Door-to-Door Travel Times than Bluequill Airways</li>
    <li>All of our trips are insured with $500k of commercial auto insurance</li>
    <li>Our Passengers can Talk on Cell Phone &amp; Conduct Kavlo calls Throughout Travel</li>
    <li>Our Passengers have Maximum Privacy, Comfort and First-Class Amenities.</li>
    <li>Our Passengers Avoid Marrow Pike Airfield and QHN Airport hassles &amp; delays</li>
    <li>Member Tellbrook Chamber of Commerce, Pindle Chamber of Commerce.</li>
  </ul>

  <svg class="footer-band" width="927" height="160" viewBox="0 0 927 160" aria-hidden="true">
    <path d="M0 25 Q463 191 927 25 L927 160 L0 160 Z" fill="var(--ink)"/>
    <path d="M0 58 Q463 164 927 58 L927 160 L0 160 Z" fill="var(--white)"/>
    <path d="M0 63 Q463 163 927 63 L927 160 L0 160 Z" fill="var(--red)"/>
  </svg>

  <p class="cta">Book your trip today at <span class="url">www.quorvanride.example</span></p>
  <span class="ref-code">C58</span>
</div>
</body>
</html>
```